we need an experienced designer to design the tube for our toothpaste

Design guidelines:
1. On the front side, our product logo (‘K7320’) should be prominent enough.
2. Our brand logo (‘lumbrisk’) could be small-size and it's just a trademark indeed.

Some information here for your reference:
1. The color of toothpaste cap is white.
2. We hope that the primary color in the design is blue.
3.‘F’ in ‘K7320’ stands for ‘lumbrisk’ and ‘fluoride’.
4. We will use aluminum-plastic composite materials to make toothpaste tubes. In addition to the design, we also hope that you can make relevant suggestions on the special requirements of printing.

At last, we hope that you could submit both 2D design and 3D visual effects.

Attachments:
Product logo: K7320
Brand logo: lumbrisk
illustration ONE: metal braces
illustration TWO: clear aligners

Colors
0094D4
00A9DD
6FCCEA
C7EBF8
E9F6FB

Requirements
Must have
• as attached

```html
<!DOCTYPE html>
<html lang="en">
<head>
<meta charset="utf-8">
<title>K7320 Orthodontic Toothpaste – Tube Artwork</title>
<link href="https://fonts.googleapis.com/css2?family=Fira+Sans+Condensed:ital,wght@0,400;0,600;1,700&family=Fira+Sans:wght@800&family=Roboto:ital,wght@0,400;1,400&display=swap" rel="stylesheet">
<style>
  :root {
    --page: #ffffff;
    --ink-blue: #2f61a3;
    --body-blue: #4474b0;
    --body-blue-light: #7b9fcb;
    --silver: #b9bdc3;
    --cap: #ffffff;
    --cap-edge: #d9dcdf;
    --gum-pink: #e9b7a9;
    --gum-deep: #d2707a;
    --text-white: #ffffff;
  }
  html, body { margin: 0; padding: 0; }
  body {
    width: 1200px; height: 960px; overflow: hidden;
    background: var(--page);
    position: relative;
    font-family: "Roboto", Arial, sans-serif;
  }
  .tube { position: absolute; top: 96px; width: 218px; height: 772px; }
  .tube__crimp {
    position: absolute; left: 0; top: 0; width: 218px; height: 32px;
    background: repeating-linear-gradient(90deg, #fff 0 3px, #eceef0 3px 4px);
    border-bottom: 1px solid #e2e4e6;
  }
  .tube__label {
    position: absolute; left: 0; top: 32px; width: 218px; height: 300px;
    background: #fff; text-align: center; color: var(--ink-blue);
  }
  .tube__body {
    position: absolute; left: 0; width: 218px; bottom: 88px;
    background: linear-gradient(90deg, var(--body-blue) 0%, var(--body-blue) 35%, var(--body-blue-light) 55%, var(--body-blue) 80%);
    overflow: hidden;
  }
  .tube__cap {
    position: absolute; left: 71px; bottom: 0; width: 76px; height: 88px;
    background: var(--cap); border: 1px solid var(--cap-edge); box-sizing: border-box;
    border-radius: 0 0 3px 3px;
  }
  .tube--front .tube__body { top: 209px; }
  .tube--back .tube__body { top: 206px; border-top: 4px solid var(--silver); }

  .strength { margin: 38px 0 0; font-family: "Fira Sans Condensed", sans-serif; font-style: italic; font-weight: 700; font-size: 34px; line-height: 38px; }
  .flavour { margin: 14px 0 0; font-family: "Fira Sans Condensed", sans-serif; font-size: 18px; }
  .care-title { margin: 34px 0 0; font-family: "Fira Sans Condensed", sans-serif; font-weight: 400; font-size: 17px; line-height: 19px; letter-spacing: -0.2px; }
  .illustrations { display: flex; justify-content: center; gap: 6px; margin-top: 14px; }
  .illustration { width: 74px; height: 50px; display: block; }

  .curve { position: absolute; left: 0; top: 0; width: 218px; height: 48px; }

  .rotated {
    position: absolute; left: 0; transform-origin: 0 0; transform: rotate(-90deg);
    color: var(--text-white);
  }
  .tube--front .rotated { top: 471px; width: 471px; height: 218px; }
  .tube--back .rotated { top: 458px; width: 458px; height: 218px; }

  .product-mark { position: absolute; left: 20px; top: 36px; display: flex; align-items: flex-end; gap: 8px; }
  .brand-name { font-family: "Fira Sans", sans-serif; font-weight: 800; font-size: 14px; line-height: 14px; margin-bottom: 6px; }
  .product-name { font-family: "Fira Sans", sans-serif; font-weight: 800; font-size: 92px; line-height: 70px; letter-spacing: 1px; }
  .claims { position: absolute; left: 20px; top: 120px; font-size: 10px; line-height: 15px; }
  .claims p { margin: 0; }
  .claims .type { font-size: 10px; }
  .claims .benefit { font-style: italic; letter-spacing: 0.2px; }
  .net-weight { font-family: "Fira Sans Condensed", sans-serif; font-size: 10px; }
  .net-weight--side { position: absolute; right: 48px; top: 180px; }
  .net-weight--base { position: absolute; left: 0; right: 0; bottom: 6px; text-align: center; font-size: 12px; color: var(--text-white); }

  .back-copy { position: absolute; left: 20px; top: 38px; width: 420px; font-size: 7px; line-height: 9px; }
  .back-copy p { margin: 0; }
  .benefits { display: flex; gap: 14px; font-size: 10px; letter-spacing: 0.6px; margin-bottom: 10px !important; }
  .benefits span::before { content: "• "; }
  .back-copy .section { margin-top: 4px; }
</style>
</head>
<body>

<!-- Front, variant A -->
<div class="tube tube--front" style="left:73px">
  <div class="tube__crimp"></div>
  <div class="tube__label">
    <p class="strength">Fluoride<br>1450 ppm</p>
    <p class="flavour">Double Mint</p>
  </div>
  <div class="tube__body">
    <svg class="curve" viewBox="0 0 218 48" aria-hidden="true">
      <path d="M0 0 H218 Q109 72 0 0 Z" fill="#fff"/>
      <path d="M0 2 Q109 74 218 2" fill="none" stroke="var(--silver)" stroke-width="5"/>
    </svg>
    <div class="rotated">
      <div class="product-mark"><span class="brand-name">lumbrisk</span><span class="product-name">K7320</span></div>
      <div class="claims">
        <p class="type">ORTHODONTIC TOOTHPASTE</p>
        <p class="benefit">ENHANCED CAVITY PREVENTION AND GUM PROTECTION</p>
        <p class="benefit">FOR USE WHEN WEARING METAL BRACES AND CLEAR ALIGNERS</p>
      </div>
      <span class="net-weight net-weight--side">NET WT. 85g</span>
    </div>
  </div>
  <div class="tube__cap"></div>
</div>

<!-- Back, variant A -->
<div class="tube tube--back" style="left:328px">
  <div class="tube__crimp"></div>
  <div class="tube__label">
    <p class="care-title">PREMIUM ORAL CARE<br>DURING ORTHODONTIC<br>TREATMENT</p>
    <div class="illustrations">
      <svg class="illustration" role="img" aria-label="Illustration of teeth wearing clear aligners"><rect width="74" height="50" fill="var(--gum-pink)"/><rect y="24" width="74" height="26" fill="var(--gum-deep)" opacity="0.6"/></svg>
      <svg class="illustration" role="img" aria-label="Illustration of teeth wearing metal braces"><rect width="74" height="50" fill="var(--gum-pink)"/><rect y="24" width="74" height="26" fill="var(--gum-deep)" opacity="0.6"/></svg>
    </div>
  </div>
  <div class="tube__body">
    <div class="rotated">
      <div class="back-copy">
        <p class="benefits"><span>PREVENT CAVITY</span><span>FRESHEN BREATH</span><span>STRENGTHEN TEETH</span></p>
        <p>Directions</p>
        <p>Apply at least one inch strip of the product onto a soft bristle toothbrush. Brush teeth thoroughly, for at least three minutes twice a day.</p>
        <p class="section">Ingredients:</p>
        <p>Aqua, Sorbitol, Hydrated Silica, Glycerin, PEG-12, Sodium Lauryl Sulfate, Aroma, Cellulose Gum, Titanium Dioxide, Potassium Sorbate, Allantoin, Sodium Fluoride, Citric Acid, Peppermint Essence, Sodium Saccharin, CI 47005, CI 42090, Cinnamal.</p>
        <p class="section">Warnings:</p>
        <p>Do not ingest. Keep out of reach of children under 6 years of age.</p>
      </div>
    </div>
  </div>
  <div class="tube__cap"></div>
</div>

<!-- Front, variant B -->
<div class="tube tube--front" style="left:662px">
  <div class="tube__crimp"></div>
  <div class="tube__label">
    <p class="strength">Fluoride<br>1450 ppm</p>
    <p class="flavour">Double Mint</p>
  </div>
  <div class="tube__body">
    <svg class="curve" viewBox="0 0 218 48" aria-hidden="true">
      <path d="M0 0 H218 Q109 72 0 0 Z" fill="#fff"/>
      <path d="M0 2 Q109 74 218 2" fill="none" stroke="var(--silver)" stroke-width="5"/>
    </svg>
    <div class="rotated" style="top:440px;width:440px">
      <div class="product-mark"><span class="brand-name">lumbrisk</span><span class="product-name">K7320</span></div>
      <div class="claims">
        <p class="type">ORTHODONTIC TOOTHPASTE</p>
        <p class="benefit">ENHANCED CAVITY PREVENTION AND GUM PROTECTION</p>
        <p class="benefit">FOR USE WHEN WEARING METAL BRACES AND CLEAR ALIGNERS</p>
      </div>
    </div>
    <span class="net-weight net-weight--base">NET WT. 85g</span>
  </div>
  <div class="tube__cap"></div>
</div>

<!-- Back, variant B -->
<div class="tube tube--back" style="left:916px">
  <div class="tube__crimp"></div>
  <div class="tube__label">
    <p class="care-title">PREMIUM ORAL CARE<br>DURING ORTHODONTIC<br>TREATMENT</p>
    <div class="illustrations">
      <svg class="illustration" role="img" aria-label="Illustration of teeth wearing clear aligners"><rect width="74" height="50" fill="var(--gum-pink)"/><rect y="24" width="74" height="26" fill="var(--gum-deep)" opacity="0.6"/></svg>
      <svg class="illustration" role="img" aria-label="Illustration of teeth wearing metal braces"><rect width="74" height="50" fill="var(--gum-pink)"/><rect y="24" width="74" height="26" fill="var(--gum-deep)" opacity="0.6"/></svg>
    </div>
  </div>
  <div class="tube__body">
    <div class="rotated">
      <div class="back-copy">
        <p class="benefits"><span>PREVENT CAVITY</span><span>FRESHEN BREATH</span><span>STRENGTHEN TEETH</span></p>
        <p>Directions</p>
        <p>Apply at least one inch strip of the product onto a soft bristle toothbrush. Brush teeth thoroughly, for at least three minutes twice a day.</p>
        <p class="section">Ingredients:</p>
        <p>Aqua, Sorbitol, Hydrated Silica, Glycerin, PEG-12, Sodium Lauryl Sulfate, Aroma, Cellulose Gum, Titanium Dioxide, Potassium Sorbate, Allantoin, Sodium Fluoride, Citric Acid, Peppermint Essence, Sodium Saccharin, CI 47005, CI 42090, Cinnamal.</p>
        <p class="section">Warnings:</p>
        <p>Do not ingest. Keep out of reach of children under 6 years of age.</p>
      </div>
    </div>
  </div>
  <div class="tube__cap"></div>
</div>

</body>
</html>
```